Redesign Craft Brewing Recipe Website

Originally built with Bootstrap just to get the site going, I am seeking a complete redesign of the sites home page and recipe page. I am an experienced web developer with no graphic background, initially just looking for psd mocks.

I prefer styles that are clean and modern, and would prefer anything that is fun, engaging, and has an organic feel to it. I currently have a cartoon rabbit as a logo, but it needs some modification/tweaking, so any help in that area would be great as well.

Current site:
http://velvetfinch.cloudpagehost.net/

Current launch page/logo:
http://www.velvetfinch.com/

I like the overall layout of the elements currently, but the design sucks.

The launch page is at the following URL

Reason: Still looking for a more modern design. Designs received so far are too similar to the original.

My site is content based and does not contain images or products. Your design should not consist of large images.

Reason: The website has very little images, so the designs need to be more text and content based. The header needs to be very small and should not contain an ad rotater.

Target Market(s)

Home brewers, Craft brewers, Microbreweries, Brewpubs

Requirements
Must have
• Web 2.0 Look and Feel, Fun, Hip, Focus on content
Should not have
• A large photo as a header

```html
<!DOCTYPE html>
<html lang="en">
<head>
<meta charset="utf-8">
<title>Velvetfinch – Latest Recipes</title>
<link href="https://fonts.googleapis.com/css2?family=Roboto:wght@300;400;500;700&family=Roboto+Condensed:wght@700&display=swap" rel="stylesheet">
<style>
:root{
  --bg:#f3f3f3;
  --panel:#ffffff;
  --line:#e2e2e2;
  --ink:#333333;
  --muted:#8a8a8a;
  --brand:#2ea4d4;
  --red:#d9464b;
  --blue:#3bb2dc;
  --purple:#a98fd3;
  --green:#9bd17a;
  --sky:#8fcbdc;
  --grey:#cfcfcf;
  --black:#0c0c0c;
}
*{box-sizing:border-box;margin:0;padding:0}
html,body{width:1029px;height:1200px;overflow:hidden;background:var(--bg)}
body{font-family:"Roboto",Arial,sans-serif;color:var(--ink)}
.page{position:relative;width:1200px;height:1400px;transform:scale(0.8575);transform-origin:0 0}

/* Sidebar */
.sidebar{position:absolute;left:0;top:0;width:368px;height:1347px;background:var(--panel);border-right:1px solid var(--line);border-bottom:1px solid var(--line)}
.brand{position:absolute;left:177px;top:108px;width:180px}
.brand-mark{position:absolute;left:45px;top:-72px;width:56px;height:56px;border-radius:50%;background:#4a4a4a}
.brand-name{font-size:32px;font-weight:500;color:var(--brand);letter-spacing:-0.5px;line-height:40px}
.brand-tagline{font-size:10px;color:var(--muted);line-height:12px;width:165px}
.nav{position:absolute;right:24px;top:207px;display:flex;flex-direction:column;align-items:flex-end;gap:4px;list-style:none}
.nav li{background:#e9e9e9;font-size:16px;font-weight:300;color:#222;padding:0 11px;height:24px;line-height:24px}
.social{position:absolute;left:250px;top:375px;display:flex;gap:7px}
.social span{width:18px;height:18px;border-radius:2px}
.field-label{position:absolute;right:28px;font-size:18px;font-weight:400;color:#333}
.field{position:absolute;left:140px;width:203px;height:31px;border:1px solid #dcdcdc;font-size:12px;color:#777;padding-left:17px;line-height:29px;background:#fff}
.field .caret{position:absolute;right:16px;top:12px;width:0;height:0;border-left:4px solid transparent;border-right:4px solid transparent;border-top:6px solid #555}
.field .dot{position:absolute;right:15px;top:10px;width:9px;height:9px;border-radius:50%;border:1px solid #888}
.field .dot::after{content:"";position:absolute;left:2px;top:2px;width:3px;height:3px;border-radius:50%;background:#222}
.range-label{position:absolute;right:26px;top:743px;font-size:12px;font-weight:500;color:#333}
.range{position:absolute;left:131px;top:770px;width:210px;height:8px;border-radius:4px;background:#e6e6e6;border:1px solid #cfcfcf}
.range-fill{position:absolute;left:56px;width:131px;top:0;height:6px;background:#8ec8ec}
.range-knob{position:absolute;top:-5px;width:12px;height:14px;background:#fafafa;border:1px solid #aaa;border-radius:2px 2px 6px 6px}
.range-scale{position:absolute;left:131px;top:792px;width:212px;font-size:10px;font-weight:500;color:#333}
.range-scale span{position:absolute}
.btn-update{position:absolute;left:216px;top:840px;width:130px;height:32px;background:linear-gradient(#3a3a3a,#151515);color:#fff;font-family:"Roboto Condensed",Arial,sans-serif;font-size:13px;line-height:32px;text-align:center;border-radius:2px}

/* Main */
.title{position:absolute;left:388px;top:108px;font-size:34px;font-weight:500;color:var(--red);letter-spacing:-0.8px}
.tabs{position:absolute;left:392px;top:161px;font-size:16px;color:#999}
.tabs .sep{color:#333;margin:0 10px}
.tabs .active{color:#222}

.recipe{position:absolute;left:392px;width:689px;height:171px;background:var(--panel);border-bottom:1px solid var(--line)}
.recipe::before{content:"";position:absolute;left:0;top:0;width:5px;height:100%;background:var(--accent)}
.recipe::after{content:"";position:absolute;left:-7px;top:27px;border-top:7px solid transparent;border-bottom:7px solid transparent;border-right:7px solid var(--accent)}
.r-purple{--accent:var(--purple)}
.r-green{--accent:var(--green)}
.r-sky{--accent:var(--sky)}
.r-grey{--accent:var(--grey)}
.recipe-thumb{position:absolute;left:20px;top:10px;width:86px;height:89px;border:1px solid #e6e6e6;background:linear-gradient(90deg,#6b7a1e 0 33%,#b8222b 33% 66%,#1d1d1d 66%);background-clip:content-box;padding:6px 12px}
.tag{position:absolute;left:20px;width:86px;height:25px;color:#fff;font-family:"Roboto Condensed",Arial,sans-serif;font-size:13px;text-align:center;line-height:25px}
.tag-method{top:108px;background:var(--red)}
.tag-style{top:136px;background:var(--blue)}
.recipe-name{position:absolute;left:120px;top:10px;font-size:24px;font-weight:300;color:#333;letter-spacing:-0.3px}
.recipe-author{position:absolute;left:121px;top:46px;font-size:13px;color:#222}
.recipe-author em{font-style:normal;color:var(--brand)}
.recipe-text{position:absolute;left:121px;top:70px;width:500px;font-size:12.5px;line-height:22px;color:#888}
.stats{position:absolute;right:0;top:0;width:62px;height:100%;background:var(--blue);color:#fff;font-size:10px;font-weight:700;text-align:center;line-height:11px}
.stats div{padding-top:6px;height:33px}
.stats .srm{position:absolute;bottom:0;left:0;width:100%;height:33px;background:var(--red);padding-top:5px}

.results{position:absolute;left:391px;top:1292px;width:690px;height:55px;background:var(--black);color:#fff;font-size:14px;font-weight:500}
.results .label{position:absolute;left:17px;top:19px}
.results .count{position:absolute;left:155px;top:19px}
.pager{position:absolute;top:16px;height:23px;background:#fff;color:#333;font-size:11px;line-height:23px;text-align:center;border-radius:2px}
.copyright{position:absolute;right:121px;top:1366px;font-size:12px;color:#333}
</style>
</head>
<body>
<div class="page">
  <aside class="sidebar">
    <div class="brand">
      <span class="brand-mark"></span>
      <div class="brand-name">Velvetfinch</div>
      <div class="brand-tagline">Easiest way to create and share craft beer recipes.</div>
    </div>
    <ul class="nav">
      <li>HOME</li><li>RECIPES</li><li>ABOUT US</li><li>OUR CLIENTS</li><li>CONTACT</li>
    </ul>
    <div class="social" aria-label="Social links">
      <span style="background:#5fb6e3"></span><span style="background:#3f63a8"></span><span style="background:#3b3b3b"></span><span style="background:#f29d33"></span>
    </div>
    <div class="field-label" style="top:423px">Search Recipes</div>
    <div class="field" style="top:452px">Stout</div>
    <div class="field-label" style="top:499px;right:26px">Match Maker</div>
    <div class="field" style="top:529px">Boil Size<span class="dot"></span></div>
    <div class="field-label" style="top:577px;right:28px">Brewing</div>
    <div class="field" style="top:606px">Extract<span class="caret"></span></div>
    <div class="field-label" style="top:654px;right:28px">Styles</div>
    <div class="field" style="top:683px">American Amber Ale<span class="caret"></span></div>
    <div class="range-label">0 Gals to 25 Gals</div>
    <div class="range"><div class="range-fill"></div><span class="range-knob" style="left:50px"></span><span class="range-knob" style="left:180px"></span></div>
    <div class="range-scale"><span style="left:3px">0</span><span style="left:34px">5</span><span style="left:74px">10</span><span style="left:116px">15</span><span style="left:159px">20</span><span style="left:193px">25</span></div>
    <div class="btn-update">UPDATE SEARCH</div>
  </aside>

  <h1 class="title">Latest Recipes</h1>
  <div class="tabs"><span>Popular</span><span class="sep">/</span><span class="active">Recent</span></div>

  <article class="recipe r-purple" style="top:205px">
    <div class="recipe-thumb" role="img" aria-label="Three bottles of mead"></div>
    <div class="tag tag-method">Extract</div><div class="tag tag-style">Sweet Mead</div>
    <h2 class="recipe-name">Oak Bastard Sweet&nbsp; Mead</h2>
    <p class="recipe-author"><em>Created by</em> Martin Hale</p>
    <p class="recipe-text">Le Lorem Ipsum est simplement du faux texte employé dans la composition mise en page avant impression. Lorem Ipsum est le faux texte merie depuis les années 1500. quand un peintre anonyme assembla ensemble des morceaux de texte pour réaliser un livre spécimen de polices de texte.</p>
    <div class="stats"><div>2.24%<br>abv</div><div>24<br>ibu</div><div>1.006<br>fb</div><div>1.022<br>og</div><div class="srm">9<br>SRM</div></div>
  </article>

  <article class="recipe r-green" style="top:386px">
    <div class="recipe-thumb" role="img" aria-label="Three bottles of mead"></div>
    <div class="tag tag-method">Extract</div><div class="tag tag-style">Sweet Mead</div>
    <h2 class="recipe-name">Oak Bastard Sweet&nbsp; Mead</h2>
    <p class="recipe-author"><em>Created by</em> Martin Hale</p>
    <p class="recipe-text">Le Lorem Ipsum est simplement du faux texte employé dans la composition mise en page avant impression. Lorem Ipsum est le faux texte merie depuis les années 1500. quand un peintre anonyme assembla ensemble des morceaux de texte pour réaliser un livre spécimen de polices de texte.</p>
    <div class="stats"><div>2.24%<br>abv</div><div>24<br>ibu</div><div>1.006<br>fb</div><div>1.022<br>og</div><div class="srm">9<br>SRM</div></div>
  </article>

  <article class="recipe r-sky" style="top:567px">
    <div class="recipe-thumb" role="img" aria-label="Three bottles of mead"></div>
    <div class="tag tag-method">Extract</div><div class="tag tag-style">Sweet Mead</div>
    <h2 class="recipe-name">Oak Bastard Sweet&nbsp; Mead</h2>
    <p class="recipe-author"><em>Created by</em> Martin Hale</p>
    <p class="recipe-text">Le Lorem Ipsum est simplement du faux texte employé dans la composition mise en page avant impression. Lorem Ipsum est le faux texte merie depuis les années 1500. quand un peintre anonyme assembla ensemble des morceaux de texte pour réaliser un livre spécimen de polices de texte.</p>
    <div class="stats"><div>2.24%<br>abv</div><div>24<br>ibu</div><div>1.006<br>fb</div><div>1.022<br>og</div><div class="srm">9<br>SRM</div></div>
  </article>

  <article class="recipe r-grey" style="top:748px">
    <div class="recipe-thumb" role="img" aria-label="Three bottles of mead"></div>
    <div class="tag tag-method">Extract</div><div class="tag tag-style">Sweet Mead</div>
    <h2 class="recipe-name">Oak Bastard Sweet&nbsp; Mead</h2>
    <p class="recipe-author"><em>Created by</em> Martin Hale</p>
    <p class="recipe-text">Le Lorem Ipsum est simplement du faux texte employé dans la composition mise en page avant impression. Lorem Ipsum est le faux texte merie depuis les années 1500. quand un peintre anonyme assembla ensemble des morceaux de texte pour réaliser un livre spécimen de polices de texte.</p>
    <div class="stats"><div>2.24%<br>abv</div><div>24<br>ibu</div><div>1.006<br>fb</div><div>1.022<br>og</div><div class="srm">9<br>SRM</div></div>
  </article>

  <article class="recipe r-purple" style="top:930px">
    <div class="recipe-thumb" role="img" aria-label="Three bottles of mead"></div>
    <div class="tag tag-method">Extract</div><div class="tag tag-style">Sweet Mead</div>
    <h2 class="recipe-name">Oak Bastard Sweet&nbsp; Mead</h2>
    <p class="recipe-author"><em>Created by</em> Martin Hale</p>
    <p class="recipe-text">Le Lorem Ipsum est simplement du faux texte employé dans la composition mise en page avant impression. Lorem Ipsum est le faux texte merie depuis les années 1500. quand un peintre anonyme assembla ensemble des morceaux de texte pour réaliser un livre spécimen de polices de texte.</p>
    <div class="stats"><div>2.24%<br>abv</div><div>24<br>ibu</div><div>1.006<br>fb</div><div>1.022<br>og</div><div class="srm">9<br>SRM</div></div>
  </article>

  <article class="recipe r-green" style="top:1111px">
    <div class="recipe-thumb" role="img" aria-label="Three bottles of mead"></div>
    <div class="tag tag-method">Extract</div><div class="tag tag-style">Sweet Mead</div>
    <h2 class="recipe-name">Oak Bastard Sweet&nbsp; Mead</h2>
    <p class="recipe-author"><em>Created by</em> Martin Hale</p>
    <p class="recipe-text">Le Lorem Ipsum est simplement du faux texte employé dans la composition mise en page avant impression. Lorem Ipsum est le faux texte merie depuis les années 1500. quand un peintre anonyme assembla ensemble des morceaux de texte pour réaliser un livre spécimen de polices de texte.</p>
    <div class="stats"><div>2.24%<br>abv</div><div>24<br>ibu</div><div>1.006<br>fb</div><div>1.022<br>og</div><div class="srm">9<br>SRM</div></div>
  </article>

  <div class="results">
    <span class="label">Search Result</span>
    <span class="count">12 Found</span>
    <span class="pager" style="left:565px;width:47px">Prev</span>
    <span class="pager" style="left:624px;width:48px">Next</span>
  </div>
  <p class="copyright">Copyright 2013 Website Name. All Rights Reserved.</p>
</div>
</body>
</html>
```